Need Website Design for Non-Profit Veteran Site

I am looking for a very talented creative website designer for a modern feel. I'll give a little bit of guidance around what I am looking for and then your creative juices should kick in and design away. I have already purchased the domain but will need hosting (at least temporarily) and the creative design work done.The website domain is militarydocs.orgI am looking to attract current and veteran military providers (doctors, nurse practitioners, physician assistants, etc) to join and signup for membership. They would pay a yearly fee to join. Would need membership categories $135 for Provider, $55 Student, $100 for Retired, and Organization (Organization would be broken down into Less than 100 ($200), 100-249 ($250), 250-499 ($300), 500-999 ($400), 1,000-2,999 ($500), and 3,000 ($700). Would need Benefit built out and would need to accept money through CoinVane and other means. Since it's a new organization just starting, would also need a Donate button to get people to donate if they want any amount they would like. The second part of the website is that once they join, they will have acess to a list of all other providers who have registered within the website (not exportable) so they can connect with one another. If they want to see contact information this will be included in their fee as a benefit to socialize with one another. As part of the website, there will be another Veteran's portal so veterans who would like to connect with a provider around a particular speciality can reach out and request help from the doctor writing a nexus letter or letter to support the veteran who is filing a claim with the BQ. Veterans would pay a yearly sign-up fee of $30.00 and would need their membership benefits displayed. They would have access to a list of veterans in their region by state and distance, and can reach out to doctors to get their help. If a doctor and veteran agree, sharable inforamtion of medical hipaa documents can be exchanged via the website. The physician and veteran can negotiate a fee through the website only and share their details. This is a separate fee for this type of process between the provider and veteran. We will collect a $250 fee for admin on each of these and each project the veteran does with the provider will cost $450 (so essentially the doctor gets paid $450 and i get $250.00. This model could be changed over time as we start to test this out). A good example of 50% of what I'm looking for is something like the following website: https://www.lpkt.org/ It has some of the features but not all and my site should be more modernized to attract the veteran and military providers.

Target Market(s)

Current and retired military providers and veterans

Industry/Entity Type

Non Profit

Number of Pages Required

1 page

Requirements
Must have
• Military Design
• Modern Feel (Example templates for feel -https://quillmoth.com/free-photoshop-psd-web-design-template/)
• Donation box
• Stuff mentioned in the description)
Nice to have
• Open to feedback
Should not have
• Open to feedback

```html
<!DOCTYPE html>
<html lang="en">
<head>
<meta charset="UTF-8">
<title>Harborwell Net — Veteran Military Providers</title>
<link rel="stylesheet" href="https://fonts.googleapis.com/css2?family=Montserrat:wght@400;500;600;700;800&family=Open+Sans:wght@400;600&display=swap">
<style>
:root{
  --green-deep:#173a14;
  --green-nav:#2c4a1c;
  --green-brand:#1f6a23;
  --green-olive:#34452f;
  --orange:#f5820f;
  --camo-light:#e6e9e3;
  --camo-soft:#dde1d9;
  --ink:#333333;
  --ink-soft:#555555;
  --white:#ffffff;
  --footer:#0f170c;
}
*{margin:0;padding:0;box-sizing:border-box}
html,body{width:1200px;height:2394px;overflow:hidden}
body{font-family:"Open Sans",Arial,sans-serif;color:var(--ink);background:var(--white);position:relative}
a{color:inherit;text-decoration:none}

/* Header */
.site-header{position:absolute;left:0;top:0;width:1200px;height:118px;
  background:linear-gradient(135deg,#4c5a3a 0%,#3a4a2c 30%,#5b5f44 55%,#33432a 80%,#4a5538 100%)}
.brand{position:absolute;left:126px;top:38px;font-family:"Montserrat",sans-serif;font-weight:600;font-size:34px;letter-spacing:1px;color:var(--white)}
.search{position:absolute;left:667px;top:53px;width:265px;height:35px;background:#e9e9e9;display:flex;align-items:center;padding:0 14px;font-size:12px;color:#444}
.search svg{position:absolute;right:12px;top:9px}
.join-btn{position:absolute;left:945px;top:53px;width:108px;height:35px;background:var(--orange);color:var(--white);font-size:14px;display:flex;align-items:center;justify-content:center}

/* Navigation */
.main-nav{position:absolute;left:0;top:118px;width:1200px;height:51px;background:var(--green-nav)}
.main-nav ul{list-style:none;position:absolute;left:132px;width:944px;height:51px;display:flex;justify-content:space-between;align-items:center}
.main-nav a{display:block;font-size:16.5px;color:var(--white);line-height:51px}
.main-nav .active a{background:#8a9a82;padding:0 20px}

/* Hero */
.hero{position:absolute;left:0;top:169px;width:1200px;height:495px;
  background:linear-gradient(100deg,#3f5a2f 0%,#6a7a55 25%,#8d8a72 45%,#5d7a45 70%,#2f5a22 100%)}
.hero-title{position:absolute;left:0;width:1200px;top:148px;text-align:center;color:var(--white);font-family:"Montserrat",sans-serif;font-weight:700;font-size:51px;letter-spacing:.5px}
.hero-sub{position:absolute;left:0;width:1200px;top:210px;text-align:center;color:var(--white);font-family:"Montserrat",sans-serif;font-weight:700;font-size:35px}
.slider-dots{position:absolute;left:522px;top:455px;display:flex;gap:8px}
.slider-dots span{width:32px;height:4px;background:var(--white)}
.slider-dots span.current{background:#3aa0d8}

/* About */
.about{position:absolute;left:0;top:664px;width:1200px;height:432px;
  background:linear-gradient(160deg,var(--camo-light) 0%,var(--camo-soft) 100%)}
.about h2{position:absolute;left:147px;top:72px;font-family:"Montserrat",sans-serif;font-weight:400;font-size:35px;color:#333}
.about p{position:absolute;left:147px;width:450px;font-size:15.5px;line-height:26px;color:var(--ink-soft)}
.about .p1{top:136px}
.about .p2{top:201px}
.btn-solid{position:absolute;left:147px;top:310px;width:174px;height:46px;background:var(--green-brand);color:var(--white);font-family:"Montserrat",sans-serif;font-weight:600;font-size:15px;display:flex;align-items:center;justify-content:center}
.about-photo{position:absolute;left:594px;top:22px;width:491px;height:410px;
  background:linear-gradient(90deg,#8a7a55 0%,#6b6a48 45%,#dfe6ee 55%,#f2f4f6 100%)}

/* Services */
.services{position:absolute;left:0;top:1096px;width:1200px;height:388px;
  background:radial-gradient(ellipse at 50% 60%,#1f5a1c 0%,#173f14 55%,#0f240d 100%)}
.service{position:absolute;top:56px;width:300px;text-align:center;color:var(--white)}
.service .icon{width:114px;height:114px;margin:0 auto;border-radius:50%;background:var(--green-brand);border:3px solid #3b8a36;display:flex;align-items:center;justify-content:center}
.service h3{font-weight:400;font-size:21.5px;margin-top:10px}
.service p{font-size:12.5px;line-height:20px;color:#b9c8b3;margin:8px auto 0;width:280px}
.btn-outline{display:flex;margin:22px auto 0;width:166px;height:48px;border:2px solid var(--white);align-items:center;justify-content:center;font-family:"Montserrat",sans-serif;font-weight:600;font-size:14.5px;color:var(--white)}
.svc-member{left:118px}
.svc-donate{left:453px;top:48px}
.svc-veterans{left:785px}

/* Feature cards */
.features{position:absolute;left:0;top:1484px;width:1200px;height:524px;
  background:linear-gradient(200deg,var(--camo-light) 0%,var(--camo-soft) 100%)}
.card{position:absolute;top:63px;width:312px;height:400px;color:var(--white)}
.card .card-photo{height:201px}
.card .card-body{height:199px;padding:34px 34px 0}
.card h3{font-family:"Montserrat",sans-serif;font-weight:400;font-size:20px}
.card p{font-size:13px;line-height:21px;margin-top:8px}
.card .more{display:block;margin-top:14px;font-size:15.5px}
.card .more span{color:#4ab4ea}
.card-what{left:113px}
.card-what .card-body{background:var(--green-brand)}
.card-what .card-photo{background:linear-gradient(120deg,#dfe3e6 0%,#b8b0a3 45%,#e9ecef 100%)}
.card-why{left:440px}
.card-why .card-body{background:var(--green-olive);padding-top:30px}
.card-why .card-photo{background:linear-gradient(120deg,#e7e9ea 0%,#9aa6b0 50%,#f1f2f3 100%)}
.news{position:absolute;left:766px;top:66px;width:311px;height:397px;background:var(--white);box-shadow:0 1px 4px rgba(0,0,0,.18)}
.news h3{margin:14px 0 0 14px;width:285px;height:46px;background:var(--green-brand);color:var(--white);font-family:"Montserrat",sans-serif;font-weight:400;font-size:19px;line-height:46px;padding-left:24px}
.news ul{list-style:none}
.news li{position:absolute;left:51px;width:240px;font-size:13px;line-height:21px;color:var(--ink-soft)}
.news li svg{position:absolute;left:-17px;top:5px}

/* Footer */
.site-footer{position:absolute;left:0;top:2008px;width:1200px;height:386px;
  background:linear-gradient(180deg,#1f2c17 0%,#2b3f1e 40%,#3a4d26 62%,#0b1008 78%,var(--footer) 100%)}
.footer-col{position:absolute;top:63px;color:var(--white)}
.footer-col h4{font-family:"Montserrat",sans-serif;font-weight:500;font-size:17.5px}
.footer-col ul{list-style:none;margin-top:12px}
.footer-col li{font-size:14px;line-height:29px}
.col-quick{left:152px}
.col-sub{left:377px}
.col-res{left:584px}
.col-follow{left:822px}
.social-list{display:grid;grid-template-columns:repeat(2,auto);column-gap:28px}
.social-list li{display:flex;align-items:center;gap:8px}
.social-list li::before{content:"";width:12px;height:12px;border:2px solid var(--white);border-radius:50%}
.copyright{position:absolute;left:0;width:1200px;top:333px;text-align:center;font-size:12.5px;color:#6f7766}
</style>
</head>
<body>

<header class="site-header">
  <div class="brand">HARBORWELL NET</div>
  <div class="search">Search here
    <svg width="17" height="17" viewBox="0 0 17 17"><circle cx="7" cy="7" r="5.5" fill="none" stroke="#2d3a25" stroke-width="2.2"/><line x1="11" y1="11" x2="16" y2="16" stroke="#2d3a25" stroke-width="2.4"/></svg>
  </div>
  <a class="join-btn" href="#">Join Now</a>
</header>

<nav class="main-nav">
  <ul>
    <li class="active"><a href="#">Home</a></li>
    <li><a href="#">About Us</a></li>
    <li><a href="#">Services Provide</a></li>
    <li><a href="#">What We Do</a></li>
    <li><a href="#">Donate</a></li>
    <li><a href="#">Blogs</a></li>
    <li><a href="#">Publications</a></li>
    <li><a href="#">Press Room</a></li>
    <li><a href="#">Contact</a></li>
  </ul>
</nav>

<section class="hero" role="img" aria-label="Photo of a soldier holding a small flag embracing a child outdoors among trees">
  <h1 class="hero-title">VETERAN MILITARY PROVIDERS</h1>
  <p class="hero-sub">CURABITUR VEL MI SIT AMET MAGN</p>
  <div class="slider-dots"><span></span><span></span><span class="current"></span><span></span></div>
</section>

<section class="about">
  <h2>About Harborwell Net</h2>
  <p class="p1">Fusce ultricies orci ac feugiat suscipit leo massa sodales velit et scelerisque mi tortor at ipsum cligula augue</p>
  <p class="p2">bibendum accumsan vestibulum ut commodo a mi Morbi ornare gravida elit Integer congue augue et malesuada iaculis ipsum dui aliquet felis at cursus magna</p>
  <a class="btn-solid" href="#">LEARN MORE</a>
  <div class="about-photo" role="img" aria-label="Photo of a soldier in camouflage uniform and a doctor in a white coat standing with arms crossed"></div>
</section>

<section class="services">
  <div class="service svc-member">
    <div class="icon">
      <svg width="56" height="52" viewBox="0 0 56 52" fill="none" stroke="#fff" stroke-width="2.5"><rect x="3" y="3" width="50" height="34"/><line x1="28" y1="37" x2="28" y2="46"/><line x1="16" y1="47" x2="40" y2="47"/><rect x="10" y="10" width="12" height="12"/><line x1="27" y1="12" x2="46" y2="12"/><line x1="27" y1="19" x2="46" y2="19"/><line x1="10" y1="28" x2="46" y2="28"/></svg>
    </div>
    <h3>Signup for Membership</h3>
    <p>citi sociosqu ad litora torquent per conubia nostra per inceptos hymenaeos Proin nulla arcu nonummy luctus dictum</p>
    <a class="btn-outline" href="#">SIGN UP</a>
  </div>
  <div class="service svc-donate">
    <div class="icon">
      <svg width="58" height="50" viewBox="0 0 58 50" fill="#fff"><path d="M29 2 C29 2 21 13 21 18 a8 8 0 0 0 16 0 C37 13 29 2 29 2Z"/><path d="M4 34 h12 l10 -4 h12 a3 3 0 0 1 0 6 h-10 h14 l10 -8 a3 3 0 0 1 4 4 l-12 12 h-26 l-6 -3 h-8Z"/></svg>
    </div>
    <h3>Want to&nbsp; Donate</h3>
    <p>citi sociosqu ad litora torquent per conubia nostra per inceptos hymenaeos Proin nulla arcu nonummy luctus dictum</p>
    <a class="btn-outline" href="#">DONATE NOW</a>
  </div>
  <div class="service svc-veterans">
    <div class="icon">
      <svg width="52" height="56" viewBox="0 0 52 56" fill="none" stroke="#fff" stroke-width="2.5"><rect x="12" y="3" width="28" height="18"/><line x1="21" y1="3" x2="21" y2="21"/><line x1="31" y1="3" x2="31" y2="21"/><path d="M26 21 L31 32 L43 33 L34 41 L37 53 L26 47 L15 53 L18 41 L9 33 L21 32Z"/></svg>
    </div>
    <h3>Veterans</h3>
    <p>citi sociosqu ad litora torquent per conubia nostra per inceptos hymenaeos Proin nulla arcu nonummy luctus dictum</p>
    <a class="btn-outline" href="#">SIGN UP</a>
  </div>
</section>

<section class="features">
  <article class="card card-what">
    <div class="card-photo" role="img" aria-label="Photo of a doctor helping a patient stand up in a clinic room"></div>
    <div class="card-body">
      <h3>WHAT WE DO</h3>
      <p>To connect people and organizations interests, inspiring each other and enabling together reach better results.</p>
      <a class="more" href="#">Read More <span>›</span></a>
    </div>
  </article>
  <article class="card card-why">
    <div class="card-photo" role="img" aria-label="Photo of medical staff reviewing notes on a clipboard"></div>
    <div class="card-body">
      <h3>WHY WE ARE</h3>
      <p>Proin nulla arcu nonummy luctus dictum eget fermentum et lorem Nunc porta convallis pede</p>
      <a class="more" href="#">Read More <span>›</span></a>
    </div>
  </article>
  <aside class="news">
    <h3>NEWS &amp; PRESSROOM</h3>
    <ul>
      <li style="top:84px"><svg width="8" height="11" viewBox="0 0 8 11"><path d="M1 1 L6 5.5 L1 10" fill="none" stroke="#222" stroke-width="2"/></svg>Duis quam Nam eget lacus Aliquam erat volutpat Quisque dignis</li>
      <li style="top:146px"><svg width="8" height="11" viewBox="0 0 8 11"><path d="M1 1 L6 5.5 L1 10" fill="none" stroke="#222" stroke-width="2"/></svg>Etiam est nunc venenatis in tristique eu imperdiet ac nisl Cum sociis</li>
      <li style="top:211px"><svg width="8" height="11" viewBox="0 0 8 11"><path d="M1 1 L6 5.5 L1 10" fill="none" stroke="#222" stroke-width="2"/></svg>Praesent sit amet est In dictum dolor eu dictum porttitor enim felis viverra mi eget luctus massa puru</li>
      <li style="top:303px"><svg width="8" height="11" viewBox="0 0 8 11"><path d="M1 1 L6 5.5 L1 10" fill="none" stroke="#222" stroke-width="2"/></svg>Duis quam Nam eget lacus Aliquam erat volutpat Quisque dignis</li>
    </ul>
  </aside>
</section>

<footer class="site-footer" role="img" aria-label="Silhouettes of marching soldiers against a dusk sky">
  <div class="footer-col col-quick">
    <h4>QUICK LINKS</h4>
    <ul><li>About Us</li><li>What We Do</li><li>Why Us</li><li>Research</li></ul>
  </div>
  <div class="footer-col col-sub">
    <h4>SUBLINKS</h4>
    <ul><li>News</li><li>Publications</li><li>Blogs</li><li>Contact</li></ul>
  </div>
  <div class="footer-col col-res">
    <h4>RESOURCES</h4>
    <ul><li>Jobs</li><li>Membership</li><li>Contact Us</li></ul>
  </div>
  <div class="footer-col col-follow">
    <h4>FOLLOW US</h4>
    <ul class="social-list">
      <li>Chirpline</li><li>Folkboard</li><li>Workmesh</li><li>Plusring</li><li>Snapvale</li>
    </ul>
  </div>
  <p class="copyright">© 2018 Company Name&nbsp; All right reserved&nbsp; Term of Use</p>
</footer>

</body>
</html>
```